Feature Film "look book" digital brochure

Looking for a designer to create an edgy, gritty, eye popping visual representation of my film to get interest from investors, producers and actors. Basically it would introduce the project and in about 7-9 pages; give an overview of the film, why to invest, an artistic statement and potential casting ideas and an introduction to the key crew. I have included way more images than you would ever need in the files. I've also included samples for other films and a brochure someone already did for the film just to give you an idea of how it should be structured and the text content. Visually that piece is not a good guideline because it doesn't visually rep the film which is why I"m doing this contest!
The film is called 3 by 12: the sentence of an alcoholic teacher who commits a crime she can't remember and whose chance for survival depends on an ex-drug dealer and a basketball court.
Reason: I wanted people to have more time to send samples
Independent film investors, artists
Digital

```html
<!DOCTYPE html>
<html lang="en">
<head>
<meta charset="utf-8">
<title>Statement — Look Book Spread</title>
<link rel="stylesheet" href="https://fonts.googleapis.com/css2?family=Black+Ops+One&family=PT+Sans:wght@400&display=swap">
<style>
  :root {
    --paper: #ffffff;
    --ink: #111111;
    --rule: #2a2a2a;
    --accent-red: #e8262a;
    --sign-amber: #d9a25a;
    --sign-amber-light: #e6b978;
    --sign-amber-dark: #b98440;
  }
  * { box-sizing: border-box; margin: 0; padding: 0; }
  html, body {
    width: 1200px; height: 600px; overflow: hidden;
    background: var(--paper);
  }
  .spread {
    position: relative;
    width: 1200px; height: 600px;
    background: var(--paper);
    border: 1px solid var(--rule);
    overflow: hidden;
    font-family: "PT Sans", "Myriad Pro", Arial, sans-serif;
    color: var(--ink);
  }
  .spine {
    position: absolute; left: 599px; top: 0;
    width: 1px; height: 100%;
    background: var(--rule);
  }
  .page { position: absolute; top: 0; height: 100%; width: 600px; }
  .page--left { left: 0; }
  .page--right { left: 600px; }

  .section-title {
    position: absolute; left: 47px; top: 40px;
    width: 331px;
    border-top: 6px solid var(--ink);
    border-bottom: 6px solid var(--ink);
    padding: 1px 0 0;
    font-family: "Black Ops One", "Impact", sans-serif;
    font-size: 44px; line-height: 42px;
    letter-spacing: 1px;
    text-align: center;
    color: var(--ink);
  }
  .statement {
    position: absolute; left: 47px; top: 117px;
    width: 508px;
    font-size: 15.2px; line-height: 19px;
  }
  .statement p + p { margin-top: 19px; }

  .credits {
    position: absolute; left: 55px; top: 483px;
    list-style: none;
    font-size: 10px; line-height: 13px;
  }

  .key-image {
    position: absolute; left: 150px; top: 0;
    width: 420px; height: 555px;
    background: linear-gradient(160deg, var(--sign-amber-light) 0%, var(--sign-amber) 55%, var(--sign-amber-dark) 100%);
    border-radius: 0 0 24px 6px;
    transform: skewY(5deg);
    transform-origin: top left;
  }
  .section-tab {
    position: absolute; right: 0; bottom: 0;
    width: 140px; height: 33px;
    background: var(--accent-red);
    color: var(--paper);
    font-size: 17px; line-height: 33px;
    padding-left: 17px;
  }
</style>
</head>
<body>
  <main class="spread">
    <section class="page page--left">
      <h1 class="section-title">STATEMENT</h1>
      <div class="statement">
        <p>Lorem ipsum dolor sit amet, consectetur adipiscing elit. Sed dapibus tellus id sodales vulputate. Pellentesque arcu ligula, dapibus sed eros vel, ullam­corper congue neque. Nam vel massa vel arcu rutrum gravida vel non dolor. Maecenas quis volutpat odio. Nulla sed ipsum porttitor, gravida dolor vitae, cursus ipsum. Donec et mollis dui, non ornare tortor. Pellentesque accumsan auctor arcu. Praesent semper, diam sit amet tincidunt facilisis, nisl ante dictum ante, vel volutpat odio mauris vitae arcu. Proin nec arcu est. Donec congue nunc vel neque ultricies euismod. Proin tristique arcu leo, ut tincidunt ipsum pharetra vel.</p>
        <p>Suspendisse potenti. Fusce imperdiet leo vehicula, hendrerit turpis nec, imperdiet orci. Vivamus iaculis lorem in congue vestibulum. Integer ornare bibendum sapien, sed ultricies mi luctus in. Maecenas lobortis velit eget urna tristique, at pretium nulla scelerisque. Curabitur tincidunt ut mauris et fringilla. Pellentesque habitant morbi tristique senectus et netus et malesua­da fames ac turpis egestas. In vel elementum odio. Duis in diam facilisis lectus tempor blandit sed sit amet elit. In hac habitasse platea dictumst. Suspendisse vitae eros eget orci convallis sagittis.</p>
      </div>
      <ul class="credits">
        <li>Mira Dane</li>
        <li>Tessa Lowe</li>
        <li>Cora Vantle</li>
        <li>Jules Penrose</li>
        <li>Nadia Fenwick</li>
        <li>Odette Marsh</li>
      </ul>
    </section>
    <div class="spine"></div>
    <section class="page page--right">
      <div class="key-image" role="img" aria-label="Photograph of an amber road caution sign on a post warning to reduce speed for cross traffic near a state prison"></div>
      <div class="section-tab">synopsis</div>
    </section>
  </main>
</body>
</html>
```